A renowned orthopaedic surgeon starting his own private clinic needs a business card design

I would need to have a design for an upcoming private clinic for orthopaedic practice.
The target market are patients that need to see a specialist for Bone and Joint Surgery.

The colors to be blue and white
Words to refer to the attached file.
Updates

Hi, Please refer to the files and a new attached file for the wordings and please attached a logo for the business card

thanks

Hi, card size is 88X 54mm

thanks

Reason: need more time to feedback

Reason: Need more time

Target Market(s)

Patients seeing for Shoulder, Elbow, wrist and hand
General Orthopaedics and Orthopaedics Trauma

Industry/Entity Type

Clinic

Colors
0355a3
eff4f7

Requirements
Must have
• follow wordings on namecard attached

```html
<!DOCTYPE html>
<html lang="en">
<head>
<meta charset="utf-8">
<title>Osteocrest Business Card</title>
<link href="https://fonts.googleapis.com/css2?family=Exo+2:wght@400;500;600&display=swap" rel="stylesheet">
<style>
  :root {
    --card-blue: #12a6e3;
    --card-white: #ffffff;
    --panel-white: #f4f6f7;
    --ink-dark: #2a2a2a;
    --backdrop: #e9ecef;
    --line-light: rgba(255,255,255,0.85);
  }
  * { box-sizing: border-box; margin: 0; padding: 0; }
  html, body { width: 1200px; height: 863px; overflow: hidden; }
  body {
    background: var(--backdrop);
    font-family: "Exo 2", Arial, sans-serif;
    position: relative;
  }
  .card {
    position: absolute;
    left: 290px;
    width: 620px;
    height: 380px;
    background: var(--card-blue);
    box-shadow: 0 6px 18px rgba(0,0,0,0.18);
    overflow: hidden;
  }
  .card--front { top: 31px; }
  .card--back { top: 452px; }

  .edge-tick {
    position: absolute;
    height: 2px;
    width: 34px;
    background: var(--line-light);
  }

  /* front */
  .front-panel {
    position: absolute;
    left: 62px; right: 48px; top: 12px; bottom: 12px;
    background: linear-gradient(135deg, var(--card-white), var(--panel-white));
    display: flex;
    flex-direction: column;
    align-items: center;
    justify-content: center;
  }
  .front-panel .website {
    position: absolute;
    bottom: 34px;
    font-size: 17px;
    color: var(--ink-dark);
    letter-spacing: 0.3px;
  }

  .brand { text-align: center; color: var(--card-blue); }
  .brand__name {
    font-size: 30px;
    font-weight: 600;
    letter-spacing: 2px;
    line-height: 1;
    text-transform: uppercase;
  }
  .brand__tagline {
    font-size: 13px;
    font-weight: 600;
    letter-spacing: 1.6px;
    text-transform: uppercase;
    margin-top: 4px;
  }

  /* back */
  .back-panel {
    position: absolute;
    left: 48px; top: 14px; bottom: 14px;
    width: 300px;
    background: linear-gradient(135deg, var(--card-white), var(--panel-white));
    display: flex;
    align-items: center;
    justify-content: center;
  }
  .back-panel .brand__name { font-size: 26px; }
  .back-panel .brand__tagline { font-size: 11px; }

  .details {
    position: absolute;
    left: 368px; right: 22px; top: 34px;
    color: var(--card-white);
    text-align: right;
  }
  .person__name {
    font-size: 22px;
    font-weight: 500;
    letter-spacing: 1.5px;
    text-transform: uppercase;
    line-height: 1.1;
  }
  .person__title {
    font-size: 15px;
    letter-spacing: 1.2px;
    text-transform: uppercase;
  }
  .divider {
    height: 0;
    border-top: 2px dashed var(--line-light);
    margin: 22px 0 20px -20px;
  }
  .contact-row {
    display: flex;
    justify-content: flex-end;
    align-items: center;
    gap: 10px;
    margin-bottom: 10px;
  }
  .contact-row__text { font-size: 13px; line-height: 1.25; letter-spacing: 0.5px; }
  .contact-row__icon {
    width: 26px; height: 26px;
    border-radius: 5px;
    background: var(--card-white);
    display: flex; align-items: center; justify-content: center;
    flex-shrink: 0;
  }
  .contact-row__icon svg { width: 16px; height: 16px; }
  .contact-plain {
    font-size: 13px;
    letter-spacing: 0.5px;
    line-height: 1.35;
    margin-top: 14px;
  }
</style>
</head>
<body>

<section class="card card--front" aria-label="Card front">
  <span class="edge-tick" style="left:0; top:220px; width:62px;"></span>
  <span class="edge-tick" style="right:0; top:150px; width:48px;"></span>
  <div class="front-panel">
    <div class="brand">
      <div class="brand__name">Osteocrest</div>
      <div class="brand__tagline">Bone &amp; Joint Surgery</div>
    </div>
    <div class="website">www.osteocrest.com</div>
  </div>
</section>

<section class="card card--back" aria-label="Card back">
  <span class="edge-tick" style="left:0; top:210px; width:48px;"></span>
  <div class="back-panel">
    <div class="brand">
      <div class="brand__name">Osteocrest</div>
      <div class="brand__tagline">Bone &amp; Joint Surgery</div>
    </div>
  </div>

  <div class="details">
    <div class="person__name">Daniel Reyes</div>
    <div class="person__title">Financial Advisor</div>
    <div class="divider"></div>

    <div class="contact-row">
      <div class="contact-row__text">27 Harbor Street 5th Floor,<br>Bayview</div>
      <div class="contact-row__icon">
        <svg viewBox="0 0 16 16"><path d="M8 1a5 5 0 0 0-5 5c0 3.6 5 9 5 9s5-5.4 5-9a5 5 0 0 0-5-5zm0 7a2 2 0 1 1 0-4 2 2 0 0 1 0 4z" fill="var(--card-blue)"/></svg>
      </div>
    </div>
    <div class="contact-row">
      <div class="contact-row__text">012 555 0147<br>012 555 0148</div>
      <div class="contact-row__icon">
        <svg viewBox="0 0 16 16"><path d="M4 1.5l2.3 2.8-1.3 1.6a9 9 0 0 0 5.1 5.1l1.6-1.3 2.8 2.3-1.4 2.3C7.5 14 2 8.5 1.7 2.9z" fill="var(--card-blue)"/></svg>
      </div>
    </div>
    <div class="contact-row">
      <div class="contact-row__text">hello@osteocrest.com<br>www.osteocrest.com</div>
      <div class="contact-row__icon">
        <svg viewBox="0 0 16 16" fill="none" stroke="var(--card-blue)" stroke-width="1.3"><circle cx="8" cy="8" r="6.3"/><ellipse cx="8" cy="8" rx="2.8" ry="6.3"/><line x1="1.7" y1="8" x2="14.3" y2="8"/><line x1="2.6" y1="4.8" x2="13.4" y2="4.8"/><line x1="2.6" y1="11.2" x2="13.4" y2="11.2"/></svg>
      </div>
    </div>
  </div>
</section>

</body>
</html>
```